Healthcare and Professional IT Services Company need a redesigned business card

We are a IT Services company that targets small medical practices and professional business such as Attorneys, Accounts, Architects etc. We want to communicate a professional yet friendly image using recent logo redesign here on ArtHarbor. Like to see the colors blue and orange in the design. Must use the Tall Pine Computing as displayed in the new logo - then also want to incorporate the fish logo as well.

Target Market(s)

Small medical and professional services

Industry/Entity Type

It Company

Contact Information for Business Card

The usual stuff, place for name address phone website. Also maybe our tagline which is "hooked on technology"

Requirements
Must have
• My new logo and the fish somewhere on the card

```html
<!DOCTYPE html>
<html lang="en">
<head>
<meta charset="utf-8">
<title>Tall Pine Computing – Business Card</title>
<link href="https://fonts.googleapis.com/css2?family=Open+Sans:wght@400;600;700&display=swap" rel="stylesheet">
<style>
  :root {
    --bg: #ecebe8;
    --card: #ffffff;
    --blue: #4a78c4;
    --blue-light: #5fb8e6;
    --orange: #f08a4b;
    --ink-white: #ffffff;
  }
  html, body {
    margin: 0;
    padding: 0;
    width: 1200px;
    height: 892px;
    overflow: hidden;
    background: var(--bg);
    font-family: "Open Sans", Arial, sans-serif;
  }
  .canvas {
    position: relative;
    width: 1200px;
    height: 892px;
  }
  .card {
    position: absolute;
    width: 560px;
    height: 320px;
    background: var(--card);
    box-shadow: 0 6px 18px rgba(0,0,0,0.18);
    overflow: hidden;
  }
  .card svg { display: block; }
  .card-front { left: 40px; top: 480px; }
  .card-back { left: 600px; top: 90px; }
  .brand-name {
    fill: var(--blue);
    font-weight: 600;
    font-family: "Open Sans", Arial, sans-serif;
  }
  .person-name {
    fill: var(--ink-white);
    font-size: 22px;
    font-weight: 600;
    letter-spacing: 2.5px;
    font-family: "Open Sans", Arial, sans-serif;
  }
  .contact-line {
    fill: var(--ink-white);
    font-size: 12.5px;
    font-weight: 600;
    letter-spacing: 1px;
    font-family: "Open Sans", Arial, sans-serif;
  }
</style>
</head>
<body>
<main class="canvas">

  <!-- Front of card -->
  <section class="card card-front" aria-label="Business card front">
    <svg width="560" height="320" viewBox="0 0 560 320">
      <path class="accent-stripe" d="M0,205 Q300,155 560,290" fill="none" stroke="var(--orange)" stroke-width="6"/>
      <path class="contact-band" d="M0,215 Q300,165 560,300 L560,320 L0,320 Z" fill="var(--blue)"/>

      <g class="brand-lockup">
        <circle cx="92" cy="118" r="40" fill="var(--blue-light)"/>
        <text class="brand-name" x="148" y="128" font-size="28">Tall Pine Computing</text>
      </g>

      <text class="person-name" x="24" y="262">Owen Castell</text>
      <line class="divider" x1="212" y1="232" x2="212" y2="306" stroke="var(--ink-white)" stroke-width="1.5"/>

      <g class="contact-list">
        <g class="icon-phone">
          <rect x="224" y="236" width="12" height="12" fill="var(--ink-white)"/>
          <path d="M227,238 q0,7 7,8 l1,-2 l-2,-1.5 l-1,1 q-2,-1 -3,-3 l1,-1 l-1.5,-2 Z" fill="var(--blue)"/>
        </g>
        <text class="contact-line" x="242" y="247">0412 556901</text>

        <g class="icon-web">
          <rect x="224" y="254" width="12" height="12" fill="var(--ink-white)"/>
          <circle cx="230" cy="260" r="4" fill="none" stroke="var(--blue)" stroke-width="1.2"/>
          <line x1="226" y1="260" x2="234" y2="260" stroke="var(--blue)" stroke-width="1"/>
        </g>
        <text class="contact-line" x="242" y="265">www.tallpine.com</text>

        <g class="icon-pin">
          <rect x="224" y="272" width="12" height="12" fill="var(--ink-white)"/>
          <path d="M230,282 l-3.5,-5 a3.5,3.5 0 1 1 7,0 Z" fill="var(--blue)"/>
        </g>
        <text class="contact-line" x="242" y="283">482 Harbor View Road</text>
        <text class="contact-line" x="242" y="301">Maple Bay, CA 94012</text>
      </g>
    </svg>
  </section>

  <!-- Back of card -->
  <section class="card card-back" aria-label="Business card back">
    <svg width="560" height="320" viewBox="0 0 560 320">
      <g class="brand-lockup">
        <circle cx="280" cy="105" r="48" fill="var(--blue-light)"/>
        <text class="brand-name" x="280" y="205" font-size="32" text-anchor="middle">Tall Pine Computing</text>
      </g>
      <circle class="corner-mark" cx="488" cy="258" r="32" fill="var(--blue-light)" opacity="0.5"/>
    </svg>
  </section>

</main>
</body>
</html>
```